Business Card Design

I need business cards designed for a new company i have started that makes cakes, particularly themed kids cakes with a really modern design and I would like to have my business cards reflect this. I have attached some photos of cakes I have made and would like some to be used.

Industry/Entity Type

Business

Contact Information for Business Card

Business Name: Tarts and Treats by Maren
Mobile: 0492 815 063
email: maren@tartsandtreatsbymaren.example.au
Instagram: instagram.com/tartsandtreatsbymaren/
Facebook: fb.me/tartsandtreatsbymaren

Colors
e667a6
b768aa
3276b5

Requirements
Must have
• Business Name: Tarts and Treats by Maren
• Mobile: 0492 815 063
• email: maren@tartsandtreatsbymaren.example.au
• Instagram: instagram.com/tartsandtreatsbymaren/
• Facebook: fb.me/tartsandtreatsbymaren
Nice to have
• 2 to 3 pictures of my cakes

```html
<!DOCTYPE html>
<html lang="en">
<head>
<meta charset="utf-8">
<title>Tarts and Treats by Maren – Business Card</title>
<link rel="stylesheet" href="https://fonts.googleapis.com/css2?family=Open+Sans:wght@300;400;600&display=swap">
<style>
  :root {
    --pink: #e667a6;
    --pink-light: #f08cbf;
    --pink-deep: #d9579a;
    --purple: #b768aa;
    --purple-deep: #a45a98;
    --white: #ffffff;
    --ink: #6d6d75;
    --page: #ecebee;
  }
  * { box-sizing: border-box; margin: 0; padding: 0; }
  html, body { width: 1200px; height: 843px; overflow: hidden; }
  body {
    background: var(--page);
    font-family: "Open Sans", Arial, sans-serif;
    display: flex;
    flex-direction: column;
    align-items: center;
    justify-content: center;
    gap: 40px;
  }
  .card {
    position: relative;
    width: 640px;
    height: 366px;
    border-radius: 4px;
    overflow: hidden;
    box-shadow: 0 6px 18px rgba(0,0,0,0.12);
  }

  /* Back side */
  .card--back {
    background: linear-gradient(100deg, var(--pink-deep) 0%, var(--pink-light) 45%, var(--pink) 100%);
    display: flex;
    align-items: center;
    justify-content: center;
  }
  .brand {
    display: flex;
    align-items: center;
    gap: 14px;
    font-weight: 600;
    line-height: 1.1;
  }
  .brand__dot {
    width: 34px;
    height: 34px;
    border-radius: 50%;
    flex: none;
  }
  .card--back .brand { color: var(--white); font-size: 34px; }
  .card--back .brand__dot { background: var(--white); }

  /* Front side */
  .card--front { background: var(--white); }
  .drip {
    position: absolute;
    inset: 0;
    width: 100%;
    height: 100%;
  }
  .holder {
    position: absolute;
    top: 52px;
    right: 48px;
    color: var(--white);
    text-align: left;
    width: 170px;
  }
  .holder__name {
    font-size: 22px;
    font-weight: 400;
    letter-spacing: 0.04em;
  }
  .holder__role {
    font-size: 14px;
    font-weight: 300;
    margin-top: 6px;
  }
  .card--front .brand {
    position: absolute;
    top: 80px;
    left: 40px;
    color: var(--pink);
    font-size: 27px;
    width: 250px;
  }
  .card--front .brand__dot { background: var(--purple); width: 26px; height: 26px; }

  .contacts {
    position: absolute;
    left: 40px;
    bottom: 30px;
    list-style: none;
    font-size: 13px;
    font-weight: 400;
    color: var(--ink);
    line-height: 1.75;
  }
  .contacts__label { color: var(--pink); font-weight: 600; }
  .contacts__mark {
    display: inline-block;
    width: 10px;
    height: 10px;
    border-radius: 2px;
    background: var(--pink);
    margin-right: 7px;
    vertical-align: -1px;
  }
</style>
</head>
<body>

  <section class="card card--back" aria-label="Business card, back">
    <div class="brand">
      <span class="brand__dot"></span>
      <span class="brand__name">Tarts and Treats<br>by Maren</span>
    </div>
  </section>

  <section class="card card--front" aria-label="Business card, front">
    <svg class="drip" viewBox="0 0 640 366" preserveAspectRatio="none" aria-hidden="true">
      <defs>
        <linearGradient id="dripFill" x1="0" y1="0" x2="1" y2="1">
          <stop offset="0" stop-color="var(--purple)"/>
          <stop offset="1" stop-color="var(--purple-deep)"/>
        </linearGradient>
      </defs>
      <path fill="url(#dripFill)" d="M640,0 H410 C380,0 380,42 410,50 C440,58 422,92 382,95 H318 C286,95 286,143 318,146 H362 C398,150 398,192 362,196 H332 C300,196 300,242 332,246 H402 C432,250 432,292 402,302 C372,312 382,366 412,366 H640 Z"/>
    </svg>

    <div class="holder">
      <p class="holder__name">ELLIOT PARR</p>
      <p class="holder__role">CEO/Founder</p>
    </div>

    <div class="brand">
      <span class="brand__dot"></span>
      <span class="brand__name">Tarts and Treats<br>by Maren</span>
    </div>

    <ul class="contacts">
      <li><span class="contacts__label">Mob:</span> 0492 815 063</li>
      <li><span class="contacts__mark"></span>tartsandtreatsbymaren</li>
      <li><span class="contacts__mark"></span>tartsandtreatsbymaren</li>
      <li>maren@tartsandtreatsbymaren.example.au</li>
    </ul>
  </section>

</body>
</html>
```